Re designing of website of VELTRIS Pens, an International stationary brand

We would like to re design our existing website veltrispens.com. We are leading manufacturers and exporters of stationary products. Our existence is global -selling and marketing in all 5 continents.

We are a 35year old group with focus on high quality, innovative designs and state of art manufacturing setup.

Client satisfaction by committed service and trust are the roots of our organisation.

We would like to see a website which focuses on our brand Veltris and must have an international appeal. Our target buyers would be Agents, distributors and wholesalers in various countries. Content would be similar to our existing website but designing and outlook needs to be totally different.

For the outlook we do like the following websites from our industry which can be used to draw inspiration.
1. www.duniverastationery.com
2. www.quorlapen.com
3. www.haltmivopen.com

The homepage need not be focused on the product but must emphasis on the branding of Veltris, our existence of 35years along with international presence and quality standards maintained by our organisation.
Updates

Reason: Would like to see some more concepts and designs as per artwork attached.

Target Market(s)

Wholesalers, Agents and Distributors in all countries around the world. Target market is global

Number of Pages Required

1 page

Font styles to use
Sans Serif

Requirements
Must have
• Focus on Branding, High Quality Standards, Customer Loyalty
Nice to have
• Like the outlook of the websites
• www.haltmivopen.com
• www.duniverastationery.com
• www.quorlapen.com
Should not have
• Don't like the outlook of our present website www.veltrispens.com
• It doesn't justify our brand or our product

```html
<!DOCTYPE html>
<html lang="en">
<head>
<meta charset="utf-8">
<title>Veltris – World Class Writing Instruments</title>
<link href="https://fonts.googleapis.com/css2?family=Open+Sans:wght@300;400;600;700&family=Oswald:wght@300;400&display=swap" rel="stylesheet">
<style>
:root{
  --red:#e0111b;
  --red-dark:#b50d14;
  --blue:#1aa3e0;
  --ink:#333333;
  --muted:#666666;
  --light-bg:#f2f2f2;
  --rule:#e1e1e1;
  --black:#000000;
  --white:#ffffff;
  --grey-btn:#dddddd;
}
*{box-sizing:border-box;margin:0;padding:0}
html,body{width:1200px;height:2759px;overflow:hidden}
body{font-family:"Open Sans",Arial,sans-serif;color:var(--ink);background:var(--white)}
.wrap{width:1026px;margin:0 auto;position:relative}
a{color:inherit;text-decoration:none}

/* header */
.site-header{height:102px;background:var(--red)}
.site-header .wrap{display:flex;align-items:center;height:102px}
.brand{display:flex;align-items:center;gap:10px;color:var(--white);font-size:40px;font-weight:600;letter-spacing:1px}
.brand-square{width:52px;height:52px;background:var(--white)}
.main-nav{margin-left:auto;display:flex;align-items:center;gap:34px;font-size:13px;color:var(--white);text-transform:uppercase}
.main-nav .current{font-weight:700;position:relative}
.main-nav .current::after{content:"";position:absolute;left:50%;margin-left:-3px;bottom:-18px;width:6px;height:6px;background:var(--white)}
.caret{font-size:9px;margin-left:3px}
.lang{background:var(--red-dark);padding:8px 16px;font-weight:700;font-size:12px}

/* hero */
.hero{height:387px;position:relative;overflow:hidden}
.hero-photo{position:absolute;inset:0;background:linear-gradient(100deg,#f7f4f1 0%,#efe7e1 40%,#dccbc0 70%,#c9ab9e 100%)}
.hero .wrap{padding-top:88px}
.hero-title{font-size:47px;font-weight:400;color:var(--red);letter-spacing:1px}
.hero-lead{margin-top:14px;font-size:15px;line-height:23px;color:#222;max-width:620px}
.hero-lead strong{font-weight:700}
.slider-controls{display:flex;align-items:center;gap:8px;margin-top:60px}
.dot{width:14px;height:14px;border-radius:50%;border:2px solid #777}
.dot.on{border-color:var(--red)}
.arrow-btn{width:32px;height:32px;border-radius:50%;background:rgba(255,255,255,.6);display:flex;align-items:center;justify-content:center;margin-left:6px}

/* welcome */
.intro{height:396px}
.intro .wrap{display:flex;padding-top:58px}
.welcome{width:555px;padding-right:40px;border-right:1px solid var(--rule);height:282px}
.section-h{font-size:29px;font-weight:400;color:var(--ink);letter-spacing:.5px}
.section-h em{font-style:normal;color:var(--red)}
.welcome p{font-size:11.5px;line-height:19px;color:#555;margin-top:12px}
.welcome p:first-of-type{margin-top:22px}
.events{flex:1;padding-left:28px}
.events-top{display:flex;justify-content:space-between;align-items:center}
.circle-btn{width:30px;height:30px;border-radius:50%;border:1px solid #ccc;display:inline-flex;align-items:center;justify-content:center;margin-left:6px}
.events-bar{display:flex;align-items:flex-end;justify-content:space-between;margin-top:6px;border-bottom:1px solid var(--rule);padding-bottom:6px}
.month{font-family:"Oswald",sans-serif;font-size:22px;color:#ddd}
.filters{font-size:9px;color:#999;text-align:right;text-transform:uppercase}
.filters .opts{font-style:italic;margin-bottom:6px}
.tag{background:#aaa;color:var(--white);padding:1px 4px;margin-left:3px}
.event{display:flex;border:1px solid var(--rule);border-left:4px solid var(--red);margin-top:10px;padding:8px 10px;gap:14px;height:70px;background:#fafafa}
.event + .event{margin-top:4px;border-left-color:#c51b1b}
.event.first{border-left-color:#f3a21b}
.date{font-family:"Oswald",sans-serif;font-size:32px;color:#555;line-height:1;width:60px}
.date small{display:block;font-size:9px;color:#999}
.event h4{font-family:"Oswald",sans-serif;font-weight:400;font-size:16px;color:#444}
.event p{font-size:9px;color:#999;margin-top:3px}

/* countries */
.countries{height:299px;background:var(--red);color:var(--white)}
.countries .wrap{padding-top:45px;text-align:center}
.band-title{font-size:30px;font-weight:300;letter-spacing:1px;padding-bottom:10px;border-bottom:1px solid rgba(255,255,255,.6)}
.country-list{margin-top:14px;font-weight:600;text-transform:uppercase}
.country-row{display:flex;justify-content:center;align-items:baseline;column-gap:16px;height:25.6px;white-space:nowrap}
.country-row span{font-size:10px}
.country-row .lg{font-size:17px}

/* why */
.why{height:542px;background:var(--light-bg)}
.why .wrap{padding-top:66px}
.why .section-h{text-align:center;font-size:31px}
.why-grid{display:grid;grid-template-columns:repeat(4,1fr);margin-top:30px}
.why-item{text-align:center;padding:40px 12px 0;border-right:1px solid var(--rule);height:420px}
.why-item:last-child{border-right:none}
.why-icon{width:96px;height:96px;border-radius:50%;background:var(--ink);margin:0 auto}
.why-item h3{font-size:16px;font-weight:600;line-height:25px;margin-top:28px;text-transform:uppercase;color:#222}
.why-item p{font-size:12px;line-height:20px;color:#555;margin:8px 14px 0;height:84px}
.btn{display:inline-block;font-size:12px;text-transform:uppercase;padding:8px 18px;background:var(--grey-btn);color:#444;margin-top:28px}
.btn.red{background:var(--red);color:var(--white);font-weight:700}

/* products */
.products{height:246px}
.products .wrap{display:flex;padding-top:66px}
.prod-col{width:510px}
.prod-col + .prod-col{border-left:1px solid var(--rule);padding-left:20px;width:516px}
.prod-col h2{font-size:29px;font-weight:400;display:flex;align-items:center;gap:12px;color:var(--red)}
.prod-col.promo h2{color:var(--blue)}
.grid-mark{width:22px;height:22px;display:grid;grid-template-columns:1fr 1fr;gap:3px}
.grid-mark i{background:#333}
.prod-links{display:flex;flex-wrap:wrap;align-items:baseline;column-gap:14px;row-gap:6px;margin-top:10px;font-size:12px;font-weight:600;text-transform:uppercase;color:#333}
.prod-links .hl{font-size:20px;font-weight:400;color:var(--red)}

/* distributor */
.distributor{height:296px;background:var(--blue);position:relative;overflow:hidden;color:var(--white)}
.globe{position:absolute;left:200px;top:-10px;width:800px;height:800px;border-radius:50%;background:radial-gradient(circle at 50% 40%,#5cc2ef 0%,#2aa6df 45%,#1690c8 75%,#1aa3e0 100%)}
.distributor .wrap{text-align:center;padding-top:56px}
.distributor h2{font-size:28px;font-weight:400;letter-spacing:.5px;width:580px;margin:0 auto;padding-bottom:10px;border-bottom:1px solid rgba(255,255,255,.6)}
.distributor p{font-size:11px;font-weight:700;line-height:23px;margin:16px auto 0;width:810px}
.btn-outline{display:inline-block;border:2px solid var(--white);padding:5px 16px;font-size:12px;font-weight:700;text-transform:uppercase;margin-top:18px}

/* footer */
.site-footer{height:493px;background:var(--black);color:var(--white)}
.site-footer .wrap{padding-top:118px}
.footer-cols{display:grid;grid-template-columns:repeat(4,1fr);gap:24px}
.footer-cols h4{font-size:15px;font-weight:700;text-transform:uppercase;padding-bottom:10px;border-bottom:1px solid #555;position:relative}
.footer-cols h4::after{content:"";position:absolute;left:0;bottom:-3px;width:62px;height:5px;background:var(--white)}
.footer-cols ul{list-style:none;margin-top:16px;font-size:12px;line-height:23px}
.footer-cols .news p{font-size:13px;line-height:20px;margin-top:14px}
.email-field{background:var(--white);height:38px;margin-top:18px;color:#999;font-size:12px;padding:11px 16px}
.subscribe{display:inline-flex;align-items:center;gap:8px;background:var(--red);font-size:11px;font-weight:700;text-transform:uppercase;padding:9px 18px;margin-top:12px}
.footer-bottom{display:flex;align-items:center;border-top:1px solid #333;margin-top:70px;padding-top:34px}
.footer-brand{color:#888;font-size:38px;font-weight:600;letter-spacing:1px;display:flex;align-items:center;gap:10px}
.footer-brand .brand-square{background:#888;width:46px;height:46px}
.copy{font-size:11px;color:#999;margin-left:90px}
.social{margin-left:auto;display:flex;gap:10px}
.social i{width:26px;height:26px;border-radius:50%;background:#555}
</style>
</head>
<body>

<header class="site-header">
  <div class="wrap">
    <a class="brand" href="#"><span class="brand-square"></span>VELTRIS</a>
    <nav class="main-nav">
      <a class="current" href="#">Home</a>
      <a href="#">About Us</a>
      <a href="#">Products<span class="caret">▼</span></a>
      <a href="#">Careers</a>
      <a href="#">Enquiry Form</a>
      <a href="#">Contact</a>
      <a class="lang" href="#">English<span class="caret">▼</span></a>
    </nav>
  </div>
</header>

<section class="hero">
  <div class="hero-photo" role="img" aria-label="Close-up photograph of a hand writing with a metal pen"></div>
  <div class="wrap">
    <h1 class="hero-title">VELTRIS METAL PENS</h1>
    <p class="hero-lead">We are leading manufacturers and exporters of stationary products. Our existence is global<br><strong>Selling and marketing in all 5 continents</strong></p>
    <div class="slider-controls">
      <span class="dot"></span><span class="dot"></span><span class="dot on"></span><span class="dot"></span>
      <span class="arrow-btn"><svg width="10" height="14" viewBox="0 0 10 14"><path d="M8 1 2 7l6 6" fill="none" stroke="#666" stroke-width="2"/></svg></span>
      <span class="arrow-btn"><svg width="10" height="14" viewBox="0 0 10 14"><path d="M2 1l6 6-6 6" fill="none" stroke="#aaa" stroke-width="2"/></svg></span>
    </div>
  </div>
</section>

<section class="intro">
  <div class="wrap">
    <div class="welcome">
      <h2 class="section-h">WELCOME TO <em>VELTRIS</em></h2>
      <p>Duis autem vel eum iriure dolor in hendrerit in vulputate velit esse molestie consequat, vel illum dolore eu feugiat nulla facilisis at vero eros et accumsan et iusto odio dignissim qui blandit praesent luptatum zzril delenit augue duis dolore te feugait nulla facilisi.</p>
      <p>Lorem ipsum dolor sit amet, consectetuer adipiscing elit, sed diam nonummy nibh euismod tincidunt ut laoreet dolore magna aliquam erat volutpat. Ut wisi enim ad minim veniam, quis nostrud exerci tation ullamcorper suscipit lobortis nisl ut aliquip ex ea commodo consequat. Duis autem vel eum iriure dolor in hendrerit in vulputate velit esse molestie consequat, vel illum dolore eu feugiat nulla facilisis at vero eros et accumsan et iusto odio dignissim qui blandit praesent luptatum zzril delenit augue duis dolore te feugait nulla facilisi.</p>
    </div>
    <div class="events">
      <div class="events-top">
        <h2 class="section-h">EVENTS</h2>
        <div>
          <span class="circle-btn"><svg width="8" height="12" viewBox="0 0 8 12"><path d="M6 1 1 6l5 5" fill="none" stroke="#aaa" stroke-width="1.5"/></svg></span><span class="circle-btn"><svg width="8" height="12" viewBox="0 0 8 12"><path d="M2 1l5 5-5 5" fill="none" stroke="#aaa" stroke-width="1.5"/></svg></span>
        </div>
      </div>
      <div class="events-bar">
        <span class="month">JUNE, 2014</span>
        <div class="filters">
          <div class="opts">Sort options</div>
          Sort by: Date ▾ &nbsp;| Country: <span class="tag">All</span> &nbsp;City: <span class="tag">All</span>
        </div>
      </div>
      <div class="event first">
        <div class="date">20<small>JUN · SUN</small></div>
        <div><h4>CAMPING TRIP</h4><p>9:00 am – July 15 3:00 pm</p></div>
      </div>
      <div class="event">
        <div class="date">26<small>JUN · SAT</small></div>
        <div><h4>CINCO DE MAYO</h4><p>10:00 am – 3:00 pm · 48 Alder Row, Fenwick 20415</p><p>Event organised by: Harbor Events Guild</p></div>
      </div>
    </div>
  </div>
</section>

<section class="countries">
  <div class="wrap">
    <h2 class="band-title">EXPORTING COUNTRIES</h2>
    <div class="country-list">
      <div class="country-row"><span class="lg">Argentina</span><span>Armenia</span><span>Aruba</span><span>Australia</span><span class="lg">Austria</span><span>Azerbaijan</span><span class="lg">Bahamas, The Bahrain</span><span>Bangladesh</span><span class="lg">Barbados</span></div>
      <div class="country-row"><span>Belarus</span><span>Belgium</span><span>Belize</span><span>Benin</span><span>Bhutan</span><span>Bolivia</span><span>Bosnia and Herzegovina</span><span class="lg">Botswana</span><span>Brazil</span><span>Brunei</span><span class="lg">Bulgaria</span><span>Burkina</span></div>
      <div class="country-row"><span>Cameroon</span><span class="lg">Canada</span><span>Cape Verde</span><span>Central African Republic</span><span class="lg">Chad</span><span class="lg">Chile</span><span>China</span><span>Colombia</span><span>Comoros</span><span>Congo, Democratic Republic</span></div>
      <div class="country-row"><span>of the Egypt</span><span>France</span><span>Georgia</span><span class="lg">Germany</span><span>Ghana</span><span>Haiti</span><span>Hong Kong</span><span>Hungary</span><span class="lg">India</span><span>Indonesia</span><span class="lg">Iran</span><span>Iraq</span><span>Ireland</span><span>Italy</span></div>
      <div class="country-row"><span class="lg">Jamaica</span><span>Japan</span><span class="lg">Jordan</span></div>
    </div>
  </div>
</section>

<section class="why">
  <div class="wrap">
    <h2 class="section-h">WHY CHOOSE US?</h2>
    <div class="why-grid">
      <div class="why-item">
        <div class="why-icon" role="img" aria-label="Gears icon for manufacturing"></div>
        <h3>Leading manufacturers<br>and exporters</h3>
        <p>Cero eros et accumsan et iusto odio dignissim qui blandit praesent luptatum zzril delenit augue duis dolore te feugait nulla facilisi.</p>
        <a class="btn" href="#">Read more</a>
      </div>
      <div class="why-item">
        <div class="why-icon" role="img" aria-label="Target icon for experience"></div>
        <h3>35 years of<br>experience</h3>
        <p>Duis autem vel eum iriure dolor in hendrerit in vulputate velit esse molestie consequat, vel illum dolore eu feugiat nulla facilisis .</p>
        <a class="btn red" href="#">Read more</a>
      </div>
      <div class="why-item">
        <div class="why-icon" role="img" aria-label="Award ribbon icon for quality"></div>
        <h3>High quality<br>standards</h3>
        <p>Cero eros et accumsan et iusto odio dignissim qui blandit praesent luptatum zzril delenit augue duis dolore te feugait nulla facilisi.</p>
        <a class="btn" href="#">Read more</a>
      </div>
      <div class="why-item">
        <div class="why-icon" role="img" aria-label="Handshake icon for loyalty"></div>
        <h3>Customer<br>loyalty</h3>
        <p>Duis autem vel eum iriure dolor in hendrerit in vulputate velit esse molestie consequat, vel illum dolore eu feugiat nulla facilisis .</p>
        <a class="btn" href="#">Read more</a>
      </div>
    </div>
  </div>
</section>

<section class="products">
  <div class="wrap">
    <div class="prod-col retail">
      <h2><span class="grid-mark"><i></i><i></i><i></i><i></i></span>RETAIL PRODUCTS</h2>
      <div class="prod-links">
        <a href="#">Ball pens</a><a href="#">Gel pens</a><a href="#">Metal pens</a><a class="hl" href="#">Art material</a><a href="#">Office stationery</a>
        <a href="#">Notebooks</a><a href="#">Refills</a><a href="#">Packaging</a><a href="#">POP</a>
      </div>
    </div>
    <div class="prod-col promo">
      <h2><span class="grid-mark"><i></i><i></i><i></i><i></i></span>PROMOTIONAL PRODUCTS</h2>
      <div class="prod-links">
        <a href="#">Plastic ball pens</a><a href="#">Metal ball pens</a><a href="#">Gift sets</a><a href="#">Customization</a>
      </div>
    </div>
  </div>
</section>

<section class="distributor">
  <div class="globe" role="img" aria-label="Illustration of a globe with connected network lines"></div>
  <div class="wrap">
    <h2>BECOME A DISTRIBUTOR</h2>
    <p>Lorem ipsum dolor sit amet, consectetuer adipiscing elit, sed diam nonummy nibh euismod tincidunt ut laoreet dolore magna aliquam erat volutpat. Ut wisi enim ad minim veniam, quis nostrud exerci tation ullamcorper suscipit lobortis nisl ut aliquip ex ea commodo consequat. Duis autem vel eum iriure dolor in hendrerit in vulputate velit esse molestie consequat, vel illum dolore eu feugiat nulla facilisis at vero eros et accumsan et iusto odio dignissim qui blandit praesent luptatum zzril delenit augue duis dolore te feugait nulla facilisi.</p>
    <a class="btn-outline" href="#">Contact us now!</a>
  </div>
</section>

<footer class="site-footer">
  <div class="wrap">
    <div class="footer-cols">
      <div><h4>Products</h4><ul><li>Retail Products</li><li>Promotional Products</li></ul></div>
      <div><h4>Information</h4><ul><li>Order Now!</li><li>Privacy Policy</li><li>Payment Methods</li></ul></div>
      <div><h4>Support</h4><ul><li>Contact Us</li><li>Our Company</li><li>Veltris on Friendspace</li></ul></div>
      <div class="news">
        <h4>Newsletter Subscription</h4>
        <p>Subscribe for our Newsletter and Get latest Updates ....</p>
        <div class="email-field">Email</div>
        <a class="subscribe" href="#"><svg width="12" height="10" viewBox="0 0 12 10"><path d="M0 5h10M6 1l4 4-4 4" fill="none" stroke="#fff" stroke-width="1.5"/></svg>Subscribe</a>
      </div>
    </div>
    <div class="footer-bottom">
      <span class="footer-brand"><span class="brand-square"></span>VELTRIS</span>
      <span class="copy">VELTRIS INC. PTY LTD © 2015.</span>
      <div class="social"><i></i><i></i><i></i><i></i><i></i></div>
    </div>
  </div>
</footer>

</body>
</html>
```